ambitious event and festival agency from austria needs fresh business card design

A new design is due for the new headquarters and the new challenges. We organize events for different target groups from 16 to 60 years. The design should therefore be straightforward and not confused, so we are open to new colors and the logo may also be changed. In general, however, the most interesting suggestions are the most interesting ones. after this order we are looking for more graphics for brightloom facebook instagramm homepage etc A new design is due for the new headquarters and the new challenges. We organize events for different target groups from 16 to 60 years. The design should therefore be straightforward and not confused, so we are open to new colors and the logo may also be changed. In general, however, the most interesting suggestions are the most interesting ones. after this order we are looking for more graphics for brightloom facebook instagramm homepage etc A new design is due for the new headquarters and the new challenges. We organize events for different target groups from 16 to 60 years. The design should therefore be straightforward and not confused, so we are open to new colors and the logo may also be changed. In general, however, the most interesting suggestions are the most interesting ones. after this order we are looking for more graphics for brightloom facebook instagramm homepage etc
Updates

Reason: I am sorry for this decision but i need some more time. No new designs please, there are so many good ones and I will have made a decision in the next 3 days.

Target Market(s)

Industry/Entity Type

Business

Font styles to use
Serif
Sans Serif

Colors

Designer to choose colors to be used in the design.

Requirements
Must have
Nice to have
Should not have

```html
<!DOCTYPE html>
<html lang="en">
<head>
<meta charset="utf-8">
<title>brightloom business card</title>
<link rel="stylesheet" href="https://fonts.googleapis.com/css2?family=Oswald:wght@500&family=Work+Sans:wght@300;500&display=swap">
<style>
  :root {
    --stage: #1c1c1c;
    --card-white: #ffffff;
    --card-black: #0b0b0b;
    --brand-red: #9e1b32;
    --text-grey: #8a8a8a;
    --logo-grey: #6b6b6b;
  }
  * { margin: 0; padding: 0; box-sizing: border-box; }
  html, body { width: 1200px; height: 900px; overflow: hidden; background: var(--stage); }
  .canvas {
    width: 1200px; height: 900px;
    display: flex; flex-direction: column; align-items: center; justify-content: center; gap: 50px;
  }
  .card {
    position: relative;
    width: 620px; height: 360px;
    border-radius: 26px;
    overflow: hidden;
    font-family: "Work Sans", Arial, sans-serif;
  }
  .card--back {
    background: linear-gradient(120deg, #2a2a2a 0%, var(--card-black) 55%, #000 100%);
    display: flex; align-items: center; justify-content: center;
  }
  .card--back .wordmark { font-size: 64px; color: var(--logo-grey); }
  .card--front { background: var(--card-white); }
  .wordmark {
    font-family: "Work Sans", Arial, sans-serif;
    font-weight: 500;
    letter-spacing: -0.5px;
    line-height: 1;
  }
  .card--front .wordmark {
    position: absolute; top: 48px; right: 46px;
    font-size: 46px; color: var(--brand-red);
  }
  .holder { position: absolute; left: 48px; top: 132px; }
  .holder__name {
    font-family: "Oswald", Arial, sans-serif;
    font-weight: 500; font-size: 23px; letter-spacing: 0.5px;
    color: var(--brand-red); text-transform: uppercase; line-height: 1.1;
  }
  .holder__role, .address, .contact {
    font-weight: 300; font-size: 16px; color: var(--text-grey); line-height: 1.28;
  }
  .address { margin-top: 10px; }
  .contact { list-style: none; margin-top: 8px; }
  .contact li { display: flex; align-items: center; gap: 10px; }
  .contact svg { width: 13px; height: 13px; flex: none; }
</style>
</head>
<body>
<main class="canvas">
  <section class="card card--back">
    <span class="wordmark">brightloom</span>
  </section>

  <section class="card card--front">
    <span class="wordmark">brightloom</span>
    <div class="holder">
      <h1 class="holder__name">Lukas Brenner</h1>
      <p class="holder__role">Manager</p>
      <p class="address">brightloom<br>Wiesenweg 12<br>A4600 Talheim</p>
      <ul class="contact">
        <li>
          <svg viewBox="0 0 14 14" fill="none" stroke="var(--brand-red)" stroke-width="1.3"><rect x="3.5" y="1" width="7" height="12" rx="1.2"/><line x1="6" y1="11" x2="8" y2="11"/></svg>
          + 43 660 418 273 5
        </li>
        <li>
          <svg viewBox="0 0 14 14" fill="none" stroke="var(--brand-red)" stroke-width="1.3"><rect x="1" y="3" width="12" height="8" rx="1"/><polyline points="1,3.5 7,8 13,3.5"/></svg>
          l.brenner@brightloom.eu
        </li>
        <li>
          <svg viewBox="0 0 14 14" fill="none" stroke="var(--brand-red)" stroke-width="1.2"><circle cx="7" cy="7" r="5.8"/><ellipse cx="7" cy="7" rx="2.6" ry="5.8"/><line x1="1.2" y1="7" x2="12.8" y2="7"/></svg>
          www.brightloom.eu
        </li>
      </ul>
    </div>
  </section>
</main>
</body>
</html>
```